Website Redesign using existing images, copy etc.

I'm looking for a website redesign/refresh of my current WordPress website. I would like to utilize the same photography, a new photo viewer, and an overall refresh of the entire design. This will need to be WordPress with simple accessibility to make changes as we add additional properties and make updates. We auction luxury real estate and luxury yachts for non-distressed sellers. It needs to be simple, luxurious and with ease of use for both web and especially mobile. www.BrindleHarrow.com

```html
<!DOCTYPE html>
<html lang="en">
<head>
<meta charset="utf-8">
<title>Brindle Harrow — Real Estate &amp; Yachts</title>
<link rel="stylesheet" href="https://fonts.googleapis.com/css2?family=Poppins:ital,wght@0,300;0,400;0,500;0,600;1,400&display=swap">
<style>
:root{
  --gold:#d19e2e;
  --ink:#1d1d1f;
  --text:#444;
  --band:#f2f2f2;
  --cream:#eeebe5;
  --footer:#2a2a2b;
  --white:#fff;
  --muted:#999;
}
*{box-sizing:border-box;margin:0;padding:0}
html,body{width:1200px;height:3630px;overflow:hidden}
body{position:relative;font-family:'Poppins',sans-serif;color:var(--ink);background:var(--white)}
.abs{position:absolute}
a{color:inherit;text-decoration:none}

/* header */
.site-header{left:0;top:0;width:1200px;height:98px;background:var(--white)}
.brand{left:75px;top:30px;display:flex;align-items:center;gap:14px;font-size:20px;font-weight:400;letter-spacing:6px;color:var(--ink)}
.brand-dot{width:40px;height:40px;border:2px solid var(--ink);border-radius:50%}
.main-nav{top:42px;font-size:13px;letter-spacing:.5px}
.phone{left:993px;top:40px;font-size:15px;display:flex;align-items:center;gap:7px}

/* hero */
.hero{left:0;top:98px;width:1200px;height:702px;
  background:linear-gradient(180deg,#6b8fbf 0%,#a9bfd9 28%,#2b3550 45%,#1f2a45 62%,#3a5b7c 72%,#6f8ea8 100%)}
.hero-box{left:248px;top:327px;width:703px;height:223px;border:2px solid var(--gold);background:rgba(20,24,38,.62)}
.hero-title{left:0;top:342px;width:1200px;text-align:center;color:var(--white);font-size:86px;font-weight:400;line-height:1}
.hero-sub{left:0;top:438px;width:1200px;text-align:center;color:var(--gold);font-size:37px;font-weight:400}
.pill{display:flex;align-items:center;justify-content:center;border-radius:30px;background:var(--gold);color:var(--white);font-weight:600}
.hero-btn{top:525px;height:50px;font-size:15px}

/* intro */
.intro-photo{left:74px;top:892px;width:512px;height:512px;border-radius:50%;border:7px solid #000;
  background:radial-gradient(circle at 50% 40%,#c9b89a 0%,#6f7f8f 40%,#3f6b3a 75%,#2d4a2a 100%)}
.h2{font-size:38px;font-weight:400;line-height:45px;color:var(--ink);white-space:nowrap}
.h2-wrap{white-space:normal}
.gold-sub{color:var(--gold);font-size:22px;font-weight:500}
.para{font-size:16.5px;line-height:34px;color:var(--text);font-weight:400}

/* listing band */
.band{left:0;top:1498px;width:1200px;height:122px;background:var(--band)}
.band-title{font-size:34px}
.tab{top:1538px;height:45px;width:105px;border-radius:25px;display:flex;align-items:center;justify-content:center;font-size:17px}
.tab-active{border:1.5px solid var(--gold);color:var(--gold)}
.tab-idle{border:1.5px solid var(--ink);color:var(--ink)}
.browse-link{left:921px;top:1547px;font-size:15px;font-style:italic;text-decoration:underline}

.card{top:1681px;width:513px;height:453px}
.card-label{left:0;bottom:0;width:329px;height:132px;background:rgba(255,255,255,.88);padding:22px 22px}
.card-title{font-size:34px;font-weight:400;color:var(--ink)}
.card-link{font-size:18px;color:var(--gold);text-decoration:underline;margin-top:6px;display:block}
.arrow{top:1890px}

/* about */
.about-bg{left:0;top:2224px;width:615px;height:653px;background:var(--band)}
.about-photo{left:615px;top:2224px;width:585px;height:653px;
  background:linear-gradient(180deg,#c7cdd2 0%,#9aa3a0 10%,#5c6b4a 22%,#4a5a3a 40%,#2f4c66 55%,#1f3b58 100%)}

/* featured */
.featured{left:0;top:2877px;width:1200px;height:439px;background:var(--cream)}
.press{top:3162px;height:62px;background:#b9b6b1;border-radius:4px}

/* footer */
.site-footer{left:0;top:3316px;width:1200px;height:314px;background:var(--footer)}
.foot-head{font-size:15px;color:var(--gold);font-weight:500;letter-spacing:.5px}
.foot-links{left:75px;top:3428px;display:flex;gap:43px;font-size:17px;color:var(--white)}
.foot-small{font-size:13px;color:#ccc}
.social{top:3544px;width:22px;height:22px;border-radius:50%;border:2px solid #ddd}
.field{top:3434px;height:51px;border:1px solid #bbb;border-radius:26px;color:var(--white);font-size:14px;padding:15px 22px}
</style>
</head>
<body>

<header class="abs site-header">
  <div class="abs brand"><span class="brand-dot"></span>BRINDLE HARROW</div>
  <nav>
    <a class="abs main-nav" style="left:653px">BUY</a>
    <a class="abs main-nav" style="left:720px">SELL</a>
    <a class="abs main-nav" style="left:790px">ABOUT</a>
    <a class="abs main-nav" style="left:877px">CONTACT</a>
  </nav>
  <div class="abs phone">
    <svg width="12" height="14" viewBox="0 0 24 24"><path d="M6.6 10.8a15 15 0 0 0 6.6 6.6l2.2-2.2c.3-.3.7-.4 1-.2 1.1.4 2.3.6 3.6.6.6 0 1 .4 1 1V20c0 .6-.4 1-1 1A17 17 0 0 1 3 4c0-.6.4-1 1-1h3.5c.6 0 1 .4 1 1 0 1.3.2 2.5.6 3.6.1.3 0 .7-.2 1z" fill="#1d1d1f"/></svg>
    800-555-0142
  </div>
</header>

<section>
  <div class="abs hero" role="img" aria-label="Luxury motor yacht cruising on calm blue water past waterfront homes and palm trees"></div>
  <div class="abs hero-box"></div>
  <h1 class="abs hero-title">Brindle Harrow</h1>
  <p class="abs hero-sub">Real Estate &amp; Yachts</p>
  <a class="abs pill hero-btn" style="left:318px;width:271px">Browse Upcoming Auctions</a>
  <a class="abs pill hero-btn" style="left:614px;width:272px">Browse Past Successes</a>
</section>

<section>
  <div class="abs intro-photo" role="img" aria-label="Stone luxury estate home at dusk with lit windows and a curved front walkway"></div>
  <h2 class="abs h2 h2-wrap" style="left:616px;top:968px;width:520px">Over One Billion Dollars of Auctions Marketed</h2>
  <p class="abs gold-sub" style="left:616px;top:1070px">Real Estate &amp; Yachts</p>
  <p class="abs para" style="left:616px;top:1117px;width:512px">The experience of hearing the auctioneer’s final proclamation of “SOLD!” is unparalleled. Whether it’s the initial meeting with the seller at their estate or yacht, or the triumphant raising of the paddle by the winning buyer, we relish every moment of the process and the ensuing festivities. We’re confident that you will, too.</p>
</section>

<section>
  <div class="abs band"></div>
  <h2 class="abs h2 band-title" style="left:72px;top:1535px">Buy &amp; Sold by Brindle Harrow</h2>
  <a class="abs tab tab-active" style="left:614px">Buy</a>
  <a class="abs tab tab-idle" style="left:733px">Sell</a>
  <a class="abs browse-link">Browse Upcoming Auction</a>

  <svg class="abs arrow" style="left:44px" width="18" height="36" viewBox="0 0 18 36"><path d="M15 3 3 18l12 15" fill="none" stroke="#1d1d1f" stroke-width="2.5"/></svg>
  <svg class="abs arrow" style="left:1140px" width="18" height="36" viewBox="0 0 18 36"><path d="m3 3 12 15L3 33" fill="none" stroke="#1d1d1f" stroke-width="2.5"/></svg>

  <article class="abs card" style="left:75px;background:linear-gradient(160deg,#6b8a8a 0%,#7d9a6a 35%,#b07a5a 65%,#c9b8a4 100%)" role="img" aria-label="Aerial view of a waterfront golf community with terracotta roof estates">
    <div class="abs card-label"><h3 class="card-title">Napels / Flordia</h3><a class="card-link">Success Stories</a></div>
  </article>
  <article class="abs card" style="left:614px;background:linear-gradient(100deg,#3e5a3a 0%,#9aa38c 30%,#e6e4df 55%,#c8c3ba 100%)" role="img" aria-label="Covered white veranda with wicker chairs overlooking palms and a sunset beach">
    <div class="abs card-label"><h3 class="card-title">Sanibel / Flordia</h3><a class="card-link">Success Stories</a></div>
  </article>
</section>

<section>
  <div class="abs about-bg"></div>
  <div class="abs about-photo" role="img" aria-label="Aerial view of a peninsula estate surrounded by water and autumn trees"></div>
  <h2 class="abs h2" style="left:75px;top:2320px">About Brindle Harrow</h2>
  <p class="abs para" style="left:75px;top:2383px;width:500px">Brindle Harrow is a top-tier destination for luxury property auctions, having overseen the auction marketing of numerous high-end estates and yachts. Our team of luxury home auction experts is committed to helping property owners obtain the best value for their assets while ensuring a timely sale. Whether you have an expansive compound or a metropolitan penthouse, Brindle Harrow has the necessary skills and expertise to facilitate various luxury real estate auctions.</p>
  <a class="abs pill" style="left:75px;top:2720px;width:179px;height:55px;font-size:16px;font-weight:500">Learn More</a>
</section>

<section>
  <div class="abs featured"></div>
  <h2 class="abs h2" style="left:0;top:2958px;width:1200px;text-align:center">As Featured In</h2>
  <p class="abs para" style="left:85px;top:3021px;width:1030px;text-align:center">By offering top-tier properties and vessels globally, along with strategic auction dates, exceptional marketing tactics,<br>and a diligent public relations team, even the most prominent media outlets have taken notice.<br>Check out some of our latest press features.</p>
  <div class="abs press" style="left:180px;width:106px" aria-label="Press feature"></div>
  <div class="abs press" style="left:347px;width:150px" aria-label="Press feature"></div>
  <div class="abs press" style="left:541px;width:140px;height:40px;top:3173px" aria-label="Press feature"></div>
  <div class="abs press" style="left:735px;width:123px" aria-label="Press feature"></div>
  <div class="abs press" style="left:950px;width:68px" aria-label="Press feature"></div>
</section>

<footer class="abs site-footer"></footer>
<p class="abs foot-head" style="left:75px;top:3385px">QUICK LINKS</p>
<nav class="abs foot-links"><a>Home</a><a>Buy</a><a>Sell</a><a>About</a><a>Blog</a><a>Contact</a></nav>
<p class="abs foot-small" style="left:75px;top:3480px">Copyrights© 2023. CompanyName All Rights Reserved</p>
<p class="abs foot-small" style="left:75px;top:3507px">Terms Of Service / Privacy Policy</p>
<span class="abs social" style="left:75px"></span>
<span class="abs social" style="left:120px"></span>
<span class="abs social" style="left:164px"></span>
<span class="abs social" style="left:208px"></span>
<span class="abs social" style="left:252px"></span>

<p class="abs foot-head" style="left:704px;top:3385px">SIGN UP FOR BRINDLE ALERT</p>
<div class="abs field" style="left:704px;width:210px">Name</div>
<div class="abs field" style="left:920px;width:207px">Email Address</div>
<a class="abs pill" style="left:704px;top:3498px;width:207px;height:51px;font-size:17px">Subscribe</a>

</body>
</html>
```